Engagement party email invitation

I need an invitation designed for my upcoming engagement party. I would like the attached picture to be encircled by gum leaves or some sort of garland of green leaves.

Traditional text typeface eg Sackers Gothic Light or Mrs Eaves.

Thanks
Marnie

Font styles to use
Serif
Script

```html
<!DOCTYPE html>
<html lang="en">
<head>
<meta charset="utf-8">
<title>Engagement Invitation – Marnie &amp; Thomas</title>
<link rel="stylesheet" href="https://fonts.googleapis.com/css2?family=Cormorant+Garamond:wght@500;600;700&family=Libre+Baskerville:wght@700&display=swap">
<style>
  :root {
    --paper: #f3fafa;
    --sky: #eef7f8;
    --city: #cfe3ec;
    --hill: #a9c4b4;
    --hill-deep: #8aa89c;
    --water: #c3e8ee;
    --water-deep: #a6d8e0;
    --band: rgba(255, 255, 255, 0.74);
    --gold-light: #f3d27a;
    --gold: #c88b2a;
    --gold-deep: #6e420e;
    --amp-light: #fbf7b8;
    --amp: #d6d064;
    --leaf: #5cc23a;
    --leaf-light: #a6e46c;
    --leaf-pale: #d2f0b4;
    --leaf-deep: #2e8a2a;
    --ink-shadow: rgba(60, 35, 5, 0.55);
  }
  * { margin: 0; padding: 0; box-sizing: border-box; }
  html, body { width: 1200px; height: 627px; overflow: hidden; background: #ffffff; }
  .invitation {
    position: relative;
    width: 1200px;
    height: 627px;
    overflow: hidden;
    background: var(--paper);
    font-family: "Cormorant Garamond", Georgia, serif;
  }
  .harbour-scene {
    position: absolute;
    inset: 0;
    background:
      radial-gradient(ellipse 380px 150px at 200px 290px, var(--hill-deep) 0%, rgba(138,168,156,0.6) 50%, transparent 100%),
      radial-gradient(ellipse 560px 60px at 720px 250px, var(--hill) 0%, rgba(169,196,180,0.4) 60%, transparent 100%),
      linear-gradient(180deg, var(--sky) 0%, var(--sky) 27%, var(--city) 36%, var(--hill) 46%, var(--water) 56%, var(--water-deep) 78%, var(--water) 100%);
  }
  .garland {
    position: absolute;
    inset: 0;
    width: 1200px;
    height: 627px;
  }
  .details-band {
    position: absolute;
    left: 0; right: 0;
    top: 405px; height: 132px;
    background: var(--band);
  }
  .gold-text {
    background: linear-gradient(180deg, var(--gold-light) 0%, var(--gold) 48%, var(--gold-deep) 100%);
    -webkit-background-clip: text;
    background-clip: text;
    color: transparent;
    filter: drop-shadow(1px 2px 1px var(--ink-shadow));
  }
  .line {
    position: absolute;
    left: 0; right: 0;
    text-align: center;
    white-space: nowrap;
    line-height: 1;
  }
  .hosts {
    top: 57px;
    font-size: 60px;
    font-weight: 700;
    letter-spacing: 1px;
    padding-left: 20px;
  }
  .invite-text {
    top: 133px;
    font-size: 60px;
    font-weight: 700;
    letter-spacing: 2px;
  }
  .couple {
    top: 246px;
    font-family: "Libre Baskerville", Georgia, serif;
    font-size: 112px;
    font-weight: 700;
  }
  .couple .amp {
    background: linear-gradient(180deg, var(--amp-light) 0%, var(--amp) 100%);
    -webkit-background-clip: text;
    background-clip: text;
  }
  .date {
    top: 407px;
    font-size: 56px;
    font-weight: 500;
    letter-spacing: 2px;
  }
  .venue {
    top: 474px;
    font-size: 56px;
    font-weight: 500;
    letter-spacing: 2px;
  }
</style>
</head>
<body>
  <main class="invitation">
    <div class="harbour-scene" role="img" aria-label="Soft watercolour view of a harbour with wooded hills, a distant city skyline and moored boats"></div>
    <div class="details-band"></div>

    <svg class="garland" viewBox="0 0 1200 627" role="img" aria-label="Garland of gum leaves, ferns, berries and small blue flowers framing the top right corner and lower left of the invitation">
      <defs>
        <linearGradient id="garland-top" x1="0" y1="0" x2="1" y2="1">
          <stop offset="0" stop-color="var(--leaf-pale)" stop-opacity="0.7"/>
          <stop offset="0.45" stop-color="var(--leaf)" stop-opacity="0.85"/>
          <stop offset="1" stop-color="var(--leaf-light)" stop-opacity="0.9"/>
        </linearGradient>
        <linearGradient id="garland-bottom" x1="0" y1="1" x2="1" y2="0">
          <stop offset="0" stop-color="var(--leaf-deep)" stop-opacity="0.9"/>
          <stop offset="0.5" stop-color="var(--leaf)" stop-opacity="0.7"/>
          <stop offset="1" stop-color="var(--leaf-pale)" stop-opacity="0.35"/>
        </linearGradient>
        <radialGradient id="garland-berries">
          <stop offset="0" stop-color="var(--leaf-light)" stop-opacity="0.9"/>
          <stop offset="1" stop-color="var(--leaf-light)" stop-opacity="0"/>
        </radialGradient>
      </defs>
      <path class="garland__top-right" fill="url(#garland-top)"
        d="M700 0 H1200 V395 C1178 380 1160 350 1150 320 C1120 300 1080 250 1060 200 C1010 170 960 150 930 120 C880 90 820 70 780 50 C745 40 715 20 700 0 Z"/>
      <path class="garland__bottom-left" fill="url(#garland-bottom)"
        d="M0 350 C25 370 45 400 60 420 C110 470 170 500 240 530 C330 555 420 570 520 580 C560 590 600 600 620 627 H0 Z"/>
      <ellipse class="garland__berries" cx="85" cy="290" rx="75" ry="70" fill="url(#garland-berries)"/>
    </svg>

    <p class="line hosts"><span class="gold-text">Helen &amp; Robert Ashby</span></p>
    <p class="line invite-text"><span class="gold-text">invite you to celebrate the engagement of</span></p>
    <h1 class="line couple"><span class="gold-text">Marnie <span class="amp">&amp;</span> Thomas</span></h1>
    <p class="line date"><span class="gold-text">Saturday 23 January 2021, 6.30pm</span></p>
    <p class="line venue"><span class="gold-text">14 Harbour Lane, Riverview</span></p>
  </main>
</body>
</html>
```